Business card

creative business card for newly created national firm that specializes in high-density storage for retail markets. Looking for creativity and overall theme that will differentiate from others in this unique niche ...essentially a design that will provide instant recognition as we develop our identity in the marketplace. possible initial thoughts are attached with logo separately

Retail

```html
<!DOCTYPE html>
<html lang="en">
<head>
<meta charset="utf-8">
<title>Stackwell Storage Systems – Business Card</title>
<link rel="stylesheet" href="https://fonts.googleapis.com/css2?family=Lato:ital,wght@0,400;0,700;0,900;1,400&display=swap">
<style>
  :root {
    --card-bg: #ffffff;
    --brand-band: #afdcf5;
    --brand-mark: #5ba9cf;
    --brand-name: #2a5f7a;
    --ink: #000000;
    --tagline: #24536a;
  }
  * { margin: 0; padding: 0; box-sizing: border-box; }
  html, body {
    width: 1200px;
    height: 720px;
    overflow: hidden;
    background: var(--card-bg);
  }
  .card {
    position: relative;
    width: 1200px;
    height: 720px;
    background: var(--card-bg);
    font-family: "Lato", "Gill Sans", sans-serif;
  }
  .brand-band {
    position: absolute;
    left: 163px;
    top: 0;
    width: 401px;
    height: 720px;
    background: var(--brand-band);
  }
  .brand-mark {
    position: absolute;
    left: 100px;
    top: 110px;
    width: 200px;
    height: 200px;
    background: var(--brand-mark);
  }
  .brand-name {
    position: absolute;
    left: 36px;
    top: 440px;
    width: 340px;
    font-size: 54px;
    font-weight: 400;
    line-height: 60px;
    letter-spacing: 1px;
    color: var(--brand-name);
    text-transform: uppercase;
  }
  .contact {
    position: absolute;
    left: 564px;
    right: 0;
    top: 0;
    height: 720px;
    text-align: center;
  }
  .contact-name {
    position: absolute;
    left: 0; right: 0;
    top: 200px;
    font-size: 48px;
    font-weight: 900;
    letter-spacing: 1px;
    color: var(--ink);
  }
  .contact-phone {
    position: absolute;
    left: 0; right: 0;
    top: 262px;
    font-size: 31px;
    font-weight: 400;
    color: var(--ink);
  }
  .tagline {
    position: absolute;
    left: 0; right: 0;
    top: 368px;
    font-size: 40px;
    font-style: italic;
    font-weight: 400;
    color: var(--tagline);
  }
  .website {
    position: absolute;
    left: 0; right: 0;
    top: 600px;
    font-size: 25px;
    font-style: italic;
    color: var(--ink);
  }
</style>
</head>
<body>
  <main class="card">
    <section class="brand-band">
      <div class="brand-mark" aria-hidden="true"></div>
      <h1 class="brand-name">Stackwell<br>Storage<br>Systems</h1>
    </section>
    <section class="contact">
      <p class="contact-name">DORIAN KESTLER</p>
      <p class="contact-phone">855-SHELF-PLUS</p>
      <p class="tagline">Innovate your space</p>
      <p class="website">www.stackwellstorage.com</p>
    </section>
  </main>
</body>
</html>
```